Food broker, trader, wholesaler, liquidator looking for a 5 pages website

Looking for a 5 pages website design. We are food brokers, traders, wholesaler and closeout buyer working with manufacturers, distributors, importers sell to retailers, food service operators and industrial (ingredients). We help market their products. We are a resource for those who need a solution in the distribution/selling/placement of food on the shelves, kitchens and pantries. Whether we open new accounts with new products or sell short dated inventory, we know where to go and get results.

Target Market(s)

Food manufacturers, food distributors, food brokers

Coding

Coded - Design and coding required

Number of Pages Required

4 page

Font styles to use
Serif

Requirements
Must have
• Food-food production-warehouse-Food packaging-people meeting-trucks-supermarket shelves-

```html
<!DOCTYPE html>
<html lang="en">
<head>
<meta charset="utf-8">
<title>Harborline Provisions</title>
<link href="https://fonts.googleapis.com/css2?family=Poppins:wght@400;500;600;700&family=Lato:wght@400;700&family=Roboto:wght@400;500;700&family=Roboto+Condensed:wght@400&display=swap" rel="stylesheet">
<style>
:root{
  --navy:#0c0a4f;
  --ink:#111;
  --text:#222;
  --pale:#f0f0f7;
  --card:#efeff6;
  --white:#fff;
}
*{margin:0;padding:0;box-sizing:border-box}
html,body{width:1200px;height:2910px;overflow:hidden;background:var(--white)}
body{position:relative;font-family:'Lato',sans-serif;color:var(--text)}
.abs{position:absolute}
.brand{display:flex;align-items:center;gap:10px;font-family:'Poppins',sans-serif;font-weight:600;color:var(--navy)}
.brand-dot{border-radius:50%;background:var(--navy);flex:none}
.contact-bar{display:flex;align-items:center;font-family:'Roboto',sans-serif}
.call{display:flex;align-items:center;gap:10px}
.call small{display:block;font-size:12px;color:#222}
.call strong{display:block;font-size:18px;font-weight:400;color:#111}
.follow{display:flex;align-items:center;gap:8px;margin-left:36px;font-size:13px}
.follow span.net{width:28px;height:28px;border-radius:50%;background:var(--navy);display:inline-block}
.follow span.net.sky{background:#1a9ae0}
.follow span.net.blue{background:#3b57a8}
.nav{display:flex;align-items:center;gap:26px;font-family:'Roboto',sans-serif;font-weight:500;font-size:14.5px;color:#111;letter-spacing:.2px}
.nav .active{background:var(--navy);color:#fff;border-radius:14px;padding:4px 8px}
.hero{top:115px;left:0;width:1200px;height:545px;background:radial-gradient(ellipse at 50% 45%,#5b6150 0%,#3b4238 55%,#262b25 100%)}
.hero h1{position:absolute;top:168px;width:100%;text-align:center;font-family:'Poppins',sans-serif;font-weight:700;font-size:38px;line-height:46px;color:#fff;text-transform:uppercase;letter-spacing:-.3px}
.btn{display:inline-block;border:2px solid #fff;border-radius:12px;background:var(--navy);color:#fff;font-family:'Poppins',sans-serif;font-weight:600;text-align:center;text-transform:uppercase}
.hero .btn{position:absolute;left:526px;top:283px;width:148px;height:49px;line-height:45px;font-size:17px}
.dots{position:absolute;top:487px;left:0;width:100%;display:flex;justify-content:center;align-items:center;gap:10px}
.dots i{width:6px;height:6px;border-radius:50%;background:#fff}
.dots i.on{width:12px;height:12px;background:none;border:2px solid #fff}
.section-title{position:absolute;width:100%;text-align:center;font-family:'Poppins',sans-serif;font-weight:600;color:var(--ink);text-transform:uppercase}
.rule{position:absolute;left:574px;width:52px;height:3px;background:var(--navy)}
.intro{top:790px;left:250px;width:700px;text-align:center;font-size:14.5px;line-height:20px;color:#222}
.service{top:932px;width:295px;height:226px;background:var(--card);border-radius:3px;text-align:center}
.service .badge{position:absolute;left:104px;top:-34px;width:86px;height:86px;border-radius:50%;background:var(--navy);display:flex;align-items:center;justify-content:center}
.service h3{position:absolute;top:86px;width:100%;font-family:'Poppins',sans-serif;font-weight:500;font-size:18.5px;color:#111}
.service p{position:absolute;top:124px;left:40px;width:215px;font-size:14.5px;line-height:19px;color:#222}
.welcome-photo{top:1208px;left:0;width:557px;height:492px;background:linear-gradient(135deg,#8bb163 0%,#e6702a 45%,#2fa546 80%,#1c8a36 100%)}
.welcome-panel{top:1208px;left:557px;width:643px;height:492px;background:var(--navy);color:#fff}
.welcome-panel .pre{position:absolute;left:71px;top:58px;font-family:'Poppins',sans-serif;font-size:23px}
.welcome-panel h2{position:absolute;left:71px;top:86px;font-family:'Poppins',sans-serif;font-weight:700;font-size:33px}
.welcome-panel .line{position:absolute;left:71px;top:148px;width:48px;height:3px;background:#fff}
.welcome-panel p{position:absolute;left:71px;top:186px;width:420px;font-size:16px;line-height:21.7px}
.welcome-panel .btn{position:absolute;left:71px;top:395px;width:115px;height:37px;line-height:33px;font-size:13px;border-radius:10px}
.process{top:1700px;left:0;width:1200px;height:560px;background:var(--pale)}
.step{position:absolute;width:150px;transform:translateX(-50%);text-align:center}
.step svg{display:block;margin:0 auto}
.step h4{font-family:'Roboto',sans-serif;font-weight:500;font-size:14px;color:var(--navy);margin-top:6px;text-transform:uppercase}
.step p{font-family:'Roboto',sans-serif;font-size:11px;line-height:12.6px;color:#222;margin:3px auto 0;width:118px}
.cta{top:2260px;left:0;width:1200px;height:420px;background:radial-gradient(ellipse at 50% 50%,#6a5a3c 0%,#46402f 50%,#2b2a24 100%)}
.cta h2{position:absolute;top:110px;width:100%;text-align:center;font-family:'Poppins',sans-serif;font-weight:700;font-size:35px;color:#fff;text-transform:uppercase;letter-spacing:-.5px}
.cta p{position:absolute;top:173px;width:100%;text-align:center;font-family:'Roboto Condensed',sans-serif;font-size:23px;line-height:28px;color:#fff;text-transform:uppercase}
.cta .btn{position:absolute;left:520px;top:253px;width:160px;height:48px;line-height:44px;font-size:17px}
.footer{top:2680px;left:0;width:1200px;height:230px;background:var(--pale)}
.copy{font-family:'Roboto',sans-serif;font-size:12px;color:#111}
</style>
</head>
<body>

<header>
  <div class="abs brand" style="left:133px;top:38px;font-size:15px">
    <span class="brand-dot" style="width:44px;height:44px"></span>Harborline Provisions
  </div>
  <div class="abs contact-bar" style="left:724px;top:22px">
    <div class="call">
      <svg width="28" height="28" viewBox="0 0 24 24" fill="none" stroke="#333" stroke-width="1.6"><path d="M6.5 3l3 4-2 2a12 12 0 0 0 7.5 7.5l2-2 4 3-2 3.5C11 20 4 13 3 5z"/></svg>
      <div><small>CALL US</small><strong>555.010.2040</strong></div>
    </div>
    <div class="follow">FOLLOW
      <span class="net blue" aria-label="Social profile"></span>
      <span class="net sky" aria-label="Social profile"></span>
      <span class="net" aria-label="Social profile"></span>
    </div>
  </div>
  <nav class="abs nav" style="left:576px;top:76px">
    <span class="active">HOME</span><span>ABOUT US</span><span>WHAT WE DO</span><span>GIVING BACK</span><span>CONTACT US</span>
  </nav>
</header>

<section class="abs hero" role="img" aria-label="Photo of packaged salads in clear containers">
  <h1>Harborline Provisions works<br>with food manufacturers</h1>
  <a class="btn">Read More</a>
  <div class="dots"><i></i><i></i><i class="on"></i><i></i><i></i></div>
</section>

<section>
  <h2 class="section-title" style="top:710px;font-size:24px">What We Do</h2>
  <div class="rule" style="top:755px"></div>
  <p class="abs intro">We pride ourselves in working in an easy, personal and accessible environment making our customers and vendors comfortable with us. We look forward to connecting with you and evaluating how we can assist you reaching your sales objectives. Welcome and thank you for visiting harborlineprovisions.com</p>

  <div class="abs service" style="left:133px">
    <div class="badge"><svg width="44" height="44" viewBox="0 0 44 44" fill="none" stroke="#fff" stroke-width="2.2"><rect x="6" y="6" width="32" height="22"/><path d="M11 23l7-7 5 4 9-9M28 11h4v4M22 28v4M14 40l6-8M30 40l-6-8M4 6h36"/></svg></div>
    <h3>Sales &amp; Marketing</h3>
    <p>We connect food buyers and sellers through a dedicated approach.</p>
  </div>
  <div class="abs service" style="left:450px">
    <div class="badge"><svg width="46" height="46" viewBox="0 0 46 46" fill="none" stroke="#fff" stroke-width="2"><path d="M6 6v34h36"/><path d="M12 36V26M17 36V22M22 36V24M27 36V18M32 36V20M37 36V12"/><path d="M10 22l8-7 6 4 13-11M33 8h4v4"/></svg></div>
    <h3>Trading</h3>
    <p>We purchase goods anywhere and ship them Nationwide and Export.</p>
  </div>
  <div class="abs service" style="left:772px">
    <div class="badge"><svg width="42" height="42" viewBox="0 0 42 42" fill="#fff"><path d="M8 6h20l6 6v24H8z"/><rect x="13" y="14" width="14" height="2.4" fill="#0c0a4f"/><rect x="13" y="20" width="14" height="2.4" fill="#0c0a4f"/><rect x="13" y="26" width="8" height="2.4" fill="#0c0a4f"/><path d="M30 22l8-8 3 3-8 8-4 1z" stroke="#0c0a4f" stroke-width="1.5"/></svg></div>
    <h3>Closeout/Excess Inventory</h3>
    <p>We buy closeouts and excess inventory for prisons, outlet stores and discounters.</p>
  </div>
</section>

<section>
  <div class="abs welcome-photo" role="img" aria-label="Photo of a delivery worker holding a green grocery bag with bread and vegetables"></div>
  <div class="abs welcome-panel">
    <div class="pre">Welcome to</div>
    <h2>Harborline Provisions</h2>
    <div class="line"></div>
    <p>Harborline Provisions works with food manufacturers, brand owners, distributors and wholesalers market their products. Retail, Food Service and Industrial ingredients. Founded in 2008, Harborline Provisions started with the distribution of gluten free products understanding the need to provide access to unique flavors and products for the celiac consumers. From this, we expanded into deli, dairy, groceries, frozen and beverages.</p>
    <a class="btn">Read More</a>
  </div>
</section>

<section class="abs process">
  <h2 class="section-title" style="top:48px;font-size:25px">Our Process</h2>
  <div class="rule" style="top:94px"></div>
  <svg class="abs" style="left:0;top:0" width="1200" height="560" viewBox="0 0 1200 560" fill="none" stroke="#333" stroke-width="1.3">
    <g id="diamonds">
      <rect x="280" y="190" width="152" height="152" rx="12" transform="rotate(45 356 266)"/>
      <rect x="524" y="190" width="152" height="152" rx="12" transform="rotate(45 600 266)"/>
      <rect x="769" y="190" width="152" height="152" rx="12" transform="rotate(45 845 266)"/>
      <rect x="159" y="311" width="152" height="152" rx="12" transform="rotate(45 235 387)"/>
      <rect x="401" y="311" width="152" height="152" rx="12" transform="rotate(45 477 387)"/>
      <rect x="643" y="311" width="152" height="152" rx="12" transform="rotate(45 719 387)"/>
      <rect x="882" y="311" width="152" height="152" rx="12" transform="rotate(45 958 387)"/>
    </g>
    <g stroke-width="1.2">
      <path d="M294 338l12-12M306 326v8M306 326h-8"/>
      <path d="M418 326l12 12M430 338v-8M430 338h-8"/>
      <path d="M538 338l12-12M550 326v8M550 326h-8"/>
      <path d="M660 326l12 12M672 338v-8M672 338h-8"/>
      <path d="M782 338l12-12M794 326v8M794 326h-8"/>
      <path d="M904 326l12 12M916 338v-8M916 338h-8"/>
    </g>
  </svg>

  <div class="step" style="left:356px;top:200px">
    <svg width="44" height="34" viewBox="0 0 44 34" fill="#0c0a4f"><path d="M2 32V4h6v14l9-6v6l9-6v6l9-6v20z"/><rect x="12" y="24" width="4" height="4" fill="#fff"/><rect x="20" y="24" width="4" height="4" fill="#fff"/><rect x="28" y="24" width="4" height="4" fill="#fff"/></svg>
    <h4>Food Production</h4>
    <p>Lorem ipsum dolor sit amet consectetur ad ipiscing elit sed do eiusmod.</p>
  </div>
  <div class="step" style="left:600px;top:200px">
    <svg width="46" height="34" viewBox="0 0 46 34" fill="#0c0a4f"><path d="M8 10l15-7 15 7-15 7z"/><path d="M8 12l14 7v14L8 26z"/><path d="M38 12l-14 7v14l14-7z"/><path d="M38 10l6 4-14 7-6-4z" fill="none" stroke="#0c0a4f" stroke-width="2"/></svg>
    <h4>Food Packaging</h4>
    <p>Lorem ipsum dolor sit amet consectetur ad ipiscing elit sed do eiusmod.</p>
  </div>
  <div class="step" style="left:845px;top:200px">
    <svg width="46" height="34" viewBox="0 0 46 34" fill="#0c0a4f"><rect x="4" y="6" width="26" height="18"/><path d="M30 12h8l6 7v7H30z"/><circle cx="12" cy="28" r="4"/><circle cx="36" cy="28" r="4"/><path d="M0 10h4M0 15h4M0 20h4" stroke="#0c0a4f" stroke-width="2"/></svg>
    <h4>Trucks</h4>
    <p>Lorem ipsum dolor sit amet consectetur ad ipiscing elit sed do eiusmod.</p>
  </div>
  <div class="step" style="left:235px;top:326px">
    <svg width="48" height="34" viewBox="0 0 48 34" fill="#0c0a4f"><path d="M4 22h40c0 6-9 9-20 9S4 28 4 22z"/><path d="M8 21c2-6 8-8 16-8s14 2 16 8z" fill="none" stroke="#0c0a4f" stroke-width="2"/><path d="M18 3c-2 2 2 4 0 7M24 3c-2 2 2 4 0 7M30 3c-2 2 2 4 0 7" fill="none" stroke="#0c0a4f" stroke-width="1.5"/></svg>
    <h4>Food</h4>
    <p>Lorem ipsum dolor sit amet consectetur ad ipiscing elit sed do eiusmod.</p>
  </div>
  <div class="step" style="left:477px;top:326px">
    <svg width="42" height="38" viewBox="0 0 42 38" fill="#0c0a4f"><path d="M2 12L21 2l19 10v24H2z"/><rect x="9" y="16" width="24" height="18" fill="#fff"/><rect x="12" y="19" width="18" height="3"/><rect x="12" y="25" width="18" height="3"/><rect x="12" y="31" width="18" height="3"/></svg>
    <h4>Warehouse</h4>
    <p>Lorem ipsum dolor sit amet consectetur ad ipiscing elit sed do eiusmod.</p>
  </div>
  <div class="step" style="left:719px;top:326px">
    <svg width="56" height="38" viewBox="0 0 56 38" fill="#0c0a4f"><circle cx="12" cy="10" r="4"/><circle cx="28" cy="6" r="4"/><circle cx="44" cy="10" r="4"/><path d="M6 30v-12h12v12zM22 26V12h12v14zM38 30V18h12v12z"/><rect x="4" y="26" width="48" height="3"/><path d="M10 29v8M46 29v8" stroke="#0c0a4f" stroke-width="2"/></svg>
    <h4>People Meeting</h4>
    <p>Lorem ipsum dolor sit amet consectetur ad ipiscing elit sed do eiusmod.</p>
  </div>
  <div class="step" style="left:958px;top:326px">
    <svg width="42" height="38" viewBox="0 0 42 38" fill="#0c0a4f"><path d="M4 2h34l3 9H1z"/><path d="M5 13h32v23H5z"/><rect x="9" y="17" width="9" height="19" fill="#fff"/><rect x="22" y="17" width="11" height="10" fill="#fff"/></svg>
    <h4>Supermarket Shelves</h4>
    <p>Lorem ipsum dolor sit amet consectetur ad ipiscing elit sed do eiusmod.</p>
  </div>
</section>

<section class="abs cta" role="img" aria-label="Photo of fresh produce in clear plastic containers">
  <h2>Lorem ipsum dolor sit amet</h2>
  <p>Sed ut perspiciatis unde omnis iste natus errr<br>sit voluptatem accusantium doloremque</p>
  <a class="btn">Contact Us</a>
</section>

<footer class="abs footer">
  <div class="abs brand" style="left:132px;top:58px;font-size:21px">
    <span class="brand-dot" style="width:70px;height:70px"></span>Harborline Provisions
  </div>
  <div class="abs contact-bar" style="left:722px;top:58px">
    <div class="call">
      <svg width="28" height="28" viewBox="0 0 24 24" fill="none" stroke="#333" stroke-width="1.6"><path d="M6.5 3l3 4-2 2a12 12 0 0 0 7.5 7.5l2-2 4 3-2 3.5C11 20 4 13 3 5z"/></svg>
      <div><small>CALL US</small><strong>555.010.2040</strong></div>
    </div>
    <div class="follow">FOLLOW
      <span class="net blue" aria-label="Social profile"></span>
      <span class="net sky" aria-label="Social profile"></span>
      <span class="net" aria-label="Social profile"></span>
    </div>
  </div>
  <nav class="abs nav" style="left:581px;top:125px">
    <span>HOME</span><span>ABOUT US</span><span>WHAT WE DO</span><span>GIVING BACK</span><span>CONTACT US</span>
  </nav>
  <div class="abs copy" style="right:132px;top:174px">Copyright © 2020 All Rights Reserved</div>
</footer>

</body>
</html>
```